Create an awesome website for a medical clinic

This is a new website for a doctor's office. The site should be clean and modern, easy to navigate.

This is a wellness clinic, we want to help our clients have a healthy, active lifestyle. It should be friendly and inviting, and easy for them to call or schedule an appointment.

The site should be responsive and designed using the attached Bootstrap 3 PSD.

We will provide stock photos, until then please use stock photos from:

pixelharbor.com or
framequarry.com (preferred)

Some example sites of clean and modern designs that we like:

https://tulsaspinecare.com/
http://reachpastjoints.com/
http://turninghealthier.com/

Also attached is a temporary logo you can use.

Reason: Thank you everyone for your great designs - we need a little more time so I'm extending the project.

Need extra days to review

Also, the colors in the new logo I just linked to are the final colors of the logo, so feel free to use any complimentary colors to it.

Hi everyone, The boss wants to change the layout of the site a little bit - here's the revised layout: https://www.filecrate.com/s/k9rt31vx2qp84zn/notes%2011_29_2017.pdf?dl=0 And the graphic assets you can use are here: https://www.filecrate.com/s/k9rt31vx2qp84zn/notes%2011_29_2017.pdf?dl=0 Feel free to change the background color of the "topbar", and change the icons of the "why people trust us" if you want, these are just temporary placeholders. Thanks for your patience and hard work!

Target Market(s)

People seeking medical treatment (wellness clinic)

Industry/Entity Type

Doctor

Number of Pages Required

1 page

Font styles to use
Sans Serif

Colors
0592cd
33a6d7
abd037
9bcb3c

Requirements
Must have
• The home page should have: a strong hero image/slideshow, clinic phone number should be prominent and at the top of the page (in the nav), a "what to expect" section (this is like a FAQs section - see attachment), and a strong call to action (a button to call or schedule an appointment).
• The what to expect section is useful so that prospective clients can determine if we're a good fit for them or not. It's a basic, first-step pre-qualification block of information.
• Social media icons which links to our social media profiles should be included.
Nice to have
• - Link to 3 most recent blog entries
• - Testimonials
• - How a multilevel nav menu looks.

```html
<!DOCTYPE html>
<html lang="en">
<head>
<meta charset="utf-8">
<title>Verdant Medical Clinic</title>
<link href="https://fonts.googleapis.com/css2?family=Lato:wght@400;700&family=Poppins:wght@600&family=Roboto:wght@400;500&display=swap" rel="stylesheet">
<style>
:root{
  --green:#2fa62f;
  --blue:#3b7fc4;
  --lime:#c5e842;
  --nav-start:#8dc340;
  --nav-mid:#55b37a;
  --nav-end:#0a92cd;
  --panel-blue:#0794cd;
  --panel-green:#52b266;
  --panel-lime:#8dc12c;
  --ink:#1d1d1d;
  --muted:#444;
  --ring:#c9c9c9;
  --icon:#7cb82f;
  --strip:#f4f4f4;
}
*{box-sizing:border-box;margin:0;padding:0}
html,body{width:1200px;height:949px;overflow:hidden;background:#fff}
body{position:relative;font-family:"Lato",sans-serif;color:var(--ink)}
.abs{position:absolute}

.brand{left:59px;top:30px}
.brand-name{font-family:"Lato",sans-serif;font-weight:700;font-size:31px;line-height:1;color:var(--green);letter-spacing:0.5px}
.brand-sub{font-family:"Lato",sans-serif;font-weight:700;font-size:14px;line-height:1;color:var(--green);margin-top:3px;letter-spacing:0.6px}

.icon-ring{width:37px;height:37px;border:1px solid var(--ring);border-radius:50%;display:flex;align-items:center;justify-content:center}
.contact{top:38px;display:flex;align-items:center;gap:10px;font-family:"Roboto",sans-serif}
.contact .label{font-size:11px;font-weight:500;color:#222;line-height:14px}
.contact .value{font-size:11px;color:#333;line-height:14px}
.contact-phone{left:465px}
.contact-email{left:606px}
.appointment{left:767px;top:38px;width:178px;height:37px;border:1px solid var(--ring);border-radius:19px;display:flex;align-items:center;font-family:"Roboto",sans-serif;font-size:14px;font-weight:500;color:#333}
.appointment .icon-ring{margin-left:-1px;margin-right:12px}
.social{top:38px;display:flex;gap:9px;left:965px}

.main-nav{left:59px;top:106px;width:1081px;height:68px;background:linear-gradient(90deg,var(--nav-start) 0%,var(--nav-mid) 45%,var(--nav-end) 100%)}
.main-nav a{position:absolute;top:0;height:68px;line-height:68px;font-family:"Lato",sans-serif;font-size:18.5px;color:#fff;text-decoration:none}
.main-nav .active{left:87px;width:132px;background:var(--lime);color:#222;text-align:center}

.hero{left:59px;top:174px;width:1080px;height:468px;background:
  radial-gradient(ellipse at 78% 20%,#fdfbf6 0%,rgba(253,251,246,0) 45%),
  radial-gradient(ellipse at 30% 45%,#bcd7ea 0%,rgba(188,215,234,0) 30%),
  linear-gradient(180deg,#eef0ec 0%,#e6c9a6 45%,#c99a5c 75%,#8c6a3a 100%)}
.hero-copy{left:686px;top:309px;width:455px}
.hero-title{font-family:"Poppins",sans-serif;font-weight:600;font-size:30px;line-height:38px;color:#111}
.hero-text{font-size:17px;line-height:22px;color:#111;margin-top:9px}
.hero-rule{left:684px;top:469px;width:454px;height:1px;background:#222}
.btn-schedule{left:678px;top:486px;width:151px;height:47px;border:2px solid #222;border-radius:24px;font-family:"Poppins",sans-serif;font-weight:600;font-size:19px;color:#333;display:flex;align-items:center;justify-content:center}

.feature{top:642px;height:250px;color:#fff;padding:34px 0 0 36px}
.feature-blue{left:59px;width:362px;background:var(--panel-blue)}
.feature-green{left:421px;width:359px;background:var(--panel-green)}
.feature-lime{left:780px;width:360px;background:var(--panel-lime);padding-left:40px}
.feature h2{font-family:"Roboto",sans-serif;font-weight:400;font-size:23px;line-height:26px}
.feature p{font-size:15.5px;line-height:20.5px;margin-top:19px;width:300px}
.btn-outline{position:absolute;left:36px;top:171px;width:126px;height:39px;border:1px solid #fff;border-radius:20px;display:flex;align-items:center;justify-content:center;font-size:15px}
.timing{margin-top:18px;width:253px}
.timing-row{display:flex;justify-content:space-between;font-size:15.5px;line-height:20px;padding-bottom:7px;border-bottom:1px solid rgba(255,255,255,0.9);margin-bottom:24px}
.timing-row:last-child{margin-bottom:0}
.strip{left:59px;top:892px;width:1081px;height:14px;background:var(--strip)}
.sr{position:absolute;width:1px;height:1px;overflow:hidden;clip:rect(0 0 0 0)}
</style>
</head>
<body>

<header>
  <div class="abs brand">
    <div class="brand-name">VERDANT</div>
    <div class="brand-sub">MEDICAL CLINIC</div>
  </div>

  <div class="abs contact contact-phone">
    <span class="icon-ring">
      <svg width="18" height="18" viewBox="0 0 24 24"><path fill="var(--icon)" d="M6.6 10.8a15.2 15.2 0 0 0 6.6 6.6l2.2-2.2a1 1 0 0 1 1-.25 11.4 11.4 0 0 0 3.6.57 1 1 0 0 1 1 1V20a1 1 0 0 1-1 1A17 17 0 0 1 3 4a1 1 0 0 1 1-1h3.5a1 1 0 0 1 1 1c0 1.25.2 2.45.57 3.57a1 1 0 0 1-.25 1z"/></svg>
    </span>
    <div><div class="label">Call us</div><div class="value">(044) 555 0182</div></div>
  </div>

  <div class="abs contact contact-email">
    <span class="icon-ring">
      <svg width="18" height="14" viewBox="0 0 18 14"><rect x="1" y="1" width="16" height="12" fill="var(--icon)"/><path d="M1 1l8 6 8-6M1 13l6-5M17 13l-6-5" stroke="#fff" stroke-width="1.3" fill="none"/></svg>
    </span>
    <div><div class="label">Email</div><div class="value">infoverdantcare.in</div></div>
  </div>

  <div class="abs appointment">
    <span class="icon-ring">
      <svg width="18" height="18" viewBox="0 0 20 20"><circle cx="9" cy="6" r="4" fill="var(--icon)"/><path d="M2 18a7 7 0 0 1 13 0z" fill="var(--icon)"/><circle cx="15" cy="13" r="3" fill="#fff" stroke="var(--icon)" stroke-width="1.5"/></svg>
    </span>
    Get Appointment
  </div>

  <nav class="abs social" aria-label="Social profiles">
    <span class="icon-ring"><span class="sr">Social profile 1</span></span>
    <span class="icon-ring"><span class="sr">Social profile 2</span></span>
    <span class="icon-ring"><span class="sr">Social profile 3</span></span>
    <span class="icon-ring"><span class="sr">Social profile 4</span></span>
  </nav>
</header>

<nav class="abs main-nav" aria-label="Main">
  <a class="active" href="#">Home</a>
  <a style="left:283px" href="#">About Us</a>
  <a style="left:424px" href="#">Our Patients</a>
  <a style="left:603px" href="#">Our Treatments</a>
  <a style="left:808px" href="#">Galliers</a>
  <a style="left:941px" href="#">Contact Us</a>
</nav>

<section>
  <div class="abs hero" role="img" aria-label="Photo of a smiling young woman with arms outstretched in a sunlit field of tall golden grass"></div>
  <div class="abs hero-copy">
    <h1 class="hero-title">It is a long established fact by readable content</h1>
    <p class="hero-text">There are many variations of passages of Lorem Ipsum available, but the majority have suffered alteration in some form, by injected humour,</p>
  </div>
  <div class="abs hero-rule"></div>
  <div class="abs btn-schedule">Schedule</div>
</section>

<section>
  <div class="abs feature feature-blue">
    <h2>Aublishing software</h2>
    <p>The generated Lorem Ipsum is therefore always free from repetition, injected humour, or non-characteristic.</p>
    <div class="btn-outline">Read more</div>
  </div>
  <div class="abs feature feature-green">
    <h2>Publishing software</h2>
    <p>The generated Lorem Ipsum is therefore always free from repetition, injected humour, or non-characteristic.</p>
    <div class="btn-outline">Read more</div>
  </div>
  <div class="abs feature feature-lime">
    <h2>Daily Timing</h2>
    <div class="timing">
      <div class="timing-row"><span>Monday - Friday</span><span>09.00 - 16.00</span></div>
      <div class="timing-row"><span>Saturday</span><span>09.30 - 16.00</span></div>
      <div class="timing-row"><span>Sunday</span><span>09.30 - 15.00</span></div>
    </div>
  </div>
  <div class="abs strip"></div>
</section>

</body>
</html>
```